Copper Moth Bar & Grill Takeout Menu

Please create a takeout menu using the attached dine-in menu.
Take out menu size: Tri-Fold 11x17

Industry/Entity Type

Bar & Grill (Restaurant)

Colors

Designer to choose colors to be used in the design.

Requirements
Must have
• Phone number and website. "Order Online" "Order for Delivery"
Nice to have
• Area on the back of the menu to feature happy hour specials.

```html
<!DOCTYPE html>
<html lang="en">
<head>
<meta charset="utf-8">
<title>Copper Moth Bar &amp; Grill – Takeout Menu</title>
<link href="https://fonts.googleapis.com/css2?family=Passion+One&family=Patrick+Hand&family=Montserrat:wght@400;600&family=Rye&family=Courier+Prime:wght@400;700&display=swap" rel="stylesheet">
<style>
:root{
  --teal:#3fc5d3;
  --gold:#f4b51c;
  --ink:#1f1f1f;
  --grey:#6b6b6b;
  --paper:#ffffff;
  --stage:#ececec;
}
*{margin:0;padding:0;box-sizing:border-box}
html,body{width:1200px;height:2583px;overflow:hidden;background:var(--stage)}
body{position:relative;font-family:'Montserrat',sans-serif;color:var(--ink)}
.spread{position:absolute;left:50px;width:1100px;height:712px;background:var(--paper);display:flex;box-shadow:0 12px 30px rgba(0,0,0,.18)}
.spread--outside{top:530px}
.spread--inside{top:1342px}
.panel{width:366.66px;height:100%;position:relative;padding:26px 22px;overflow:hidden}
.panel--grey{background:linear-gradient(160deg,#f1f1f1,#dcdcdc 60%,#e9e9e9)}
.box{border:1.5px solid var(--ink);padding:12px 16px 14px;position:relative}
.box::before,.box::after{content:"";position:absolute;top:-5px;width:8px;height:8px;background:var(--ink);transform:rotate(45deg)}
.box::before{left:-5px}.box::after{right:-5px}
.sec{font-family:'Passion One',sans-serif;color:var(--teal);font-size:24px;text-align:center;display:flex;align-items:center;justify-content:center;gap:10px;line-height:1;white-space:nowrap}
.sec::before,.sec::after{content:"";width:34px;height:1.5px;background:var(--teal);flex:none}
.sec--gold{color:var(--gold);font-size:21px}
.sec--gold::before,.sec--gold::after{display:none}
.sec--small{font-size:17px}
.note{font-size:8px;text-align:center;color:#333;margin:4px 0 6px;line-height:1.3}
.item{display:flex;align-items:center;font-family:'Patrick Hand',cursive;font-size:12.5px;margin-top:6px;gap:5px}
.item .name{white-space:nowrap}
.item .dots{flex:1;border-bottom:1px dotted var(--ink);height:1px;margin-top:7px}
.price{width:20px;height:20px;border-radius:50%;background:var(--teal);color:#fff;font-family:'Passion One',sans-serif;font-size:11px;display:flex;align-items:center;justify-content:center;flex:none}
.price--plain{background:none;color:var(--ink);width:auto;font-size:11px}
.desc{font-size:7.5px;color:#444;line-height:1.3;margin-top:1px}
.list{font-size:8.5px;text-align:center;line-height:1.35;margin-top:3px}
.spacer{height:10px}
/* happy hour */
.hh-title{font-family:'Rye',serif;color:var(--gold);font-size:24px;text-align:center;margin-top:14px}
.hh-time{font-size:9.5px;text-align:center;letter-spacing:.5px;margin-top:4px}
.dotted-rule{border-bottom:2px dotted var(--teal);margin:8px 0}
.art{border-radius:4px}
.hh-art{height:170px;background:radial-gradient(ellipse at 50% 45%,#8b6fb8,#c44 55%,#8a5a2b 85%,#fff 100%)}
.deals{display:flex;gap:14px;margin-top:10px}
.deal{flex:1;text-align:center}
.deal h4{font-family:'Rye',serif;font-weight:400;font-size:11px;margin-bottom:6px}
.deal .card{border:1px solid var(--ink);padding:6px 4px;font-size:8px;line-height:1.3}
.deal .card b{font-family:'Courier Prime',monospace;color:var(--gold);font-size:11px;display:block}
.contact{text-align:center;margin-top:12px}
.phone{font-family:'Passion One',sans-serif;font-size:22px;display:flex;align-items:center;justify-content:center;gap:6px}
.web{font-family:'Courier Prime',monospace;font-weight:700;font-size:14px;letter-spacing:1.5px}
.web span{color:var(--teal)}
.social{display:flex;justify-content:center;gap:5px;margin-top:6px}
.social i{width:14px;height:14px;border-radius:50%;background:var(--gold)}
/* cover */
.brand{display:flex;align-items:center;justify-content:center;gap:12px;margin-top:34px}
.brand-mark{width:30px;height:30px;border-radius:50%;background:var(--ink);flex:none}
.brand-name{font-family:'Passion One',sans-serif;font-weight:400;font-size:30px;line-height:1;color:var(--ink)}
.title{text-align:center;margin-top:34px}
.title h1{font-family:'Passion One',sans-serif;font-weight:400;font-size:46px;line-height:1;color:var(--ink)}
.title h2{font-family:'Passion One',sans-serif;font-weight:400;font-size:28px;line-height:1.1;color:var(--ink)}
.order{display:flex;align-items:center;gap:12px;margin:30px 10px 0}
.order-icon{width:62px;height:62px;border-radius:50%;background:var(--teal);flex:none}
.order p{font-family:'Passion One',sans-serif;font-size:22px;line-height:1.15}
.order p span{color:var(--gold)}
.cover-art{position:absolute;left:0;right:0;bottom:0;height:260px;background:linear-gradient(180deg,rgba(0,0,0,0),#5f7fb8 25%,#c9843a 70%,#c0532c)}
/* burgers */
.dress{display:flex;gap:10px;align-items:flex-start;margin-top:10px}
.gf{display:flex;align-items:center;justify-content:space-between;margin-top:8px;border:1px solid #888;padding:3px 6px;font-family:'Courier Prime',monospace;font-size:9px;font-style:italic}
.gf-icons{display:flex;gap:14px}
.gf-icons i{width:14px;height:14px;border-radius:50%;background:var(--gold)}
.burger{display:grid;grid-template-columns:1fr 36px 36px 36px;align-items:start;margin-top:5px}
.burger .name{font-family:'Patrick Hand',cursive;font-size:12px;line-height:1}
.burger .p{font-family:'Passion One',sans-serif;font-size:11px;text-align:center}
.tags{display:flex;gap:10px;margin-top:6px;font-size:7px}
.tags span{border:1px solid #666;padding:1px 6px}
.burgers-head{font-family:'Passion One',sans-serif;color:var(--gold);font-size:19px;line-height:1;margin-top:12px}
</style>
</head>
<body>

<section class="spread spread--outside">
  <div class="panel">
    <div class="box">
      <h3 class="sec">OTHER HANDHELDS</h3>
      <p class="note">ALL SERVED WITH HAND CUT FRIES OR SWEET POTATO FRIES.<br>PREMIUM SIDES AVAILABLE FOR AN UP CHARGE +2</p>
      <div class="item"><span class="name">Cat Club</span><span class="dots"></span><span class="price">15</span></div>
      <p class="desc">Sliced whole wheat bread with roasted garlic aioli, grilled marinated chicken breast, provolone cheese bacon, lettuce and tomato.</p>
      <div class="item"><span class="name">What's Gouda?</span><span class="dots"></span><span class="price">14</span></div>
      <p class="desc">Sliced whole wheat bread with roasted garlic aioli smoked gouda &amp; provolone cheeses, roasted red peppers &amp; portobello mushrooms.</p>
      <div class="item"><span class="name">Southwest Melt</span><span class="dots"></span><span class="price">14</span></div>
      <p class="desc">Sliced whole wheat bread with roasted garlic aioli, 3 pepper colby jack, roasted red peppers and corn.</p>
      <div class="item"><span class="name">Westover Melt</span><span class="dots"></span><span class="price">14</span></div>
      <p class="desc">Sliced whole wheat bread with roasted garlic aioli, zucchini, portobello mushrooms, red peppers, with melted brie &amp; provolone cheeses</p>
    </div>
    <div class="spacer"></div>
    <h3 class="sec sec--gold">CHEESES</h3>
    <p class="list">Vermont Cheddar | Smoked Gouda 3-Pepper Colby Jack<br>Monterey Jack | Swiss | Brie Provolone | American</p>
    <h3 class="sec sec--gold" style="margin-top:8px">CONDIMENTS</h3>
    <p class="list">Horseradish Aioli | Chipotle Crema | Roasted Garlic Aioli | Citrus Aioli Spicy Ketchup | Dijon Mustard | Yellow Mustard | Mayo | Ketchup</p>
    <h3 class="sec sec--gold" style="margin-top:8px">TOPPINGS</h3>
    <p class="list">Bacon | Shrimp | Egg | Red Onion | White Onion | Portobello Mushrooms | Roasted Corn | Roasted Red Peppers Guacamole | Pico De Gallo | Fresh or Pickled Jalapenos</p>
    <div class="spacer"></div>
    <div class="box">
      <h3 class="sec">SIDES</h3>
      <div class="item"><span class="name">Potato Salad</span><span class="dots"></span><span class="price">4</span></div>
      <div class="item" style="margin-top:10px"><span class="name">Fire Roasted Veggie</span><span class="dots"></span><span class="price">6</span></div>
      <div class="item" style="margin-top:10px"><span class="name">Brown Rice, Quinoa, &amp; Kale Medley</span><span class="dots"></span><span class="price">5</span></div>
    </div>
  </div>

  <div class="panel">
    <div class="box">
      <h3 class="sec">KIDS MENU</h3>
      <p class="note">ALL SERVED WITH FRENCH FRIES</p>
      <div class="item"><span class="name">Grilled Cheese</span><span class="dots"></span><span class="price">8</span></div>
      <div class="item" style="margin-top:10px"><span class="name">Cheese Quesadilla</span><span class="dots"></span><span class="price">8</span></div>
      <div class="item" style="margin-top:10px"><span class="name">Mac &amp; Cheese</span><span class="dots"></span><span class="price">8</span></div>
      <div class="item" style="margin-top:10px"><span class="name">Fire Roasted Veggie</span><span class="dots"></span><span class="price">10</span></div>
    </div>
    <h3 class="hh-title">HAPPY HOUR</h3>
    <p class="hh-time">⊢ WEDNESDAY - FRIDAY 5:00 PM TO 7:00 PM ⊣</p>
    <div class="dotted-rule"></div>
    <div class="art hh-art" role="img" aria-label="Illustration of cartoon characters sharing drinks around a wooden bar table"></div>
    <div class="deals">
      <div class="deal"><h4>WEDNESDAY</h4><div class="card"><b>$2.00 OFF</b>Wine &amp; Draft Beer</div></div>
      <div class="deal"><h4>THURSDAY &amp; FRIDAY</h4><div class="card"><b>$2.00 OFF</b>Wine &amp; Draft Beer<br><i>$4.00 off Cocktails</i></div></div>
    </div>
    <div class="dotted-rule"></div>
    <div class="contact">
      <div class="phone">
        <svg width="20" height="20" viewBox="0 0 24 24"><path fill="#3fc5d3" d="M6.6 10.8a15 15 0 0 0 6.6 6.6l2.2-2.2a1 1 0 0 1 1-.25 11.4 11.4 0 0 0 3.6.57 1 1 0 0 1 1 1V20a1 1 0 0 1-1 1A17 17 0 0 1 3 4a1 1 0 0 1 1-1h3.5a1 1 0 0 1 1 1c0 1.25.2 2.450.57 3.6a1 1 0 0 1-.25 1z"/></svg>
        555-014-2290
      </div>
      <div class="web">www.<span>coppermothgrill</span>.com</div>
      <div class="social"><i></i><i></i></div>
    </div>
  </div>

  <div class="panel panel--grey">
    <div class="brand"><span class="brand-mark"></span><span class="brand-name">Copper Moth Bar &amp; Grill</span></div>
    <div class="title">
      <h1>COPPER MOTH</h1>
      <h2>BAR &amp; GRILL</h2>
    </div>
    <div class="order">
      <span class="order-icon"></span>
      <p>Order <span>Online</span><br>Order for <span>Delivery</span></p>
    </div>
    <div class="cover-art" role="img" aria-label="Illustration of three cartoon diners eating burgers at a bar table with drinks"></div>
  </div>
</section>

<section class="spread spread--inside">
  <div class="panel">
    <div class="box" style="height:100%">
      <h3 class="sec">STARTERS</h3>
      <h4 class="sec sec--gold sec--small" style="margin-top:4px">Tortilla Chips</h4>
      <div class="item"><span class="name">With House-made Salsa Verde</span><span class="dots"></span><span class="price price--plain">$7</span></div>
      <div class="item" style="margin-top:2px"><span class="name">With House-made Fire Roasted Salsa</span><span class="dots"></span><span class="price price--plain">$7</span></div>
      <div class="item" style="margin-top:2px"><span class="name">With Guacamole &amp; Pico De Gallo</span><span class="dots"></span><span class="price price--plain">$8</span></div>
      <div class="item" style="margin-top:2px"><span class="name">With Queso</span><span class="dots"></span><span class="price price--plain">$8</span></div>
      <div class="item" style="margin-top:2px"><span class="name">With Chili con Queso</span><span class="dots"></span><span class="price price--plain">$9</span></div>
      <h4 class="sec sec--gold sec--small" style="margin-top:8px">WINGS</h4>
      <div class="item"><span class="name">8 pieces</span><span class="dots"></span><span class="price">14</span></div>
      <p class="desc">Flash-fried to a crispy golden brown &amp; tossed in your choice of sauce Mild Sauce, or BBQ. Your choice of ranch or blue cheese.</p>
      <h4 class="sec sec--gold sec--small" style="margin-top:8px">QUESADILLAS</h4>
      <div class="item"><span class="name">Cheddar and Monterey Jack Cheese</span><span class="dots"></span><span class="price price--plain">$12</span></div>
      <div class="item" style="margin-top:2px"><span class="name">Pulled Marinated Chicken &amp; Cheese</span><span class="dots"></span><span class="price price--plain">$14</span></div>
      <div class="item" style="margin-top:2px"><span class="name">Fire Roasted Vegetables &amp; Cheese</span><span class="dots"></span><span class="price price--plain">$14</span></div>
      <div class="item" style="margin-top:2px"><span class="name">Garlic Roasted Shrimp &amp; Cheese</span><span class="dots"></span><span class="price price--plain">$16</span></div>
      <p class="desc">All quesadillas are stuffed with roasted red peppers, black beans. Served with guacamole, pico de gallo, and chipotle crema on the side.</p>
      <h4 class="sec sec--gold sec--small" style="margin-top:8px">CLAW-FULL NACHOS</h4>
      <p class="desc">Tortilla chips, melted white queso, Cheddar &amp; Monterey Jack cheeses, pico de gallo, guacamole, chipotle sour cream, jalapenos, &amp; green onions.</p>
      <div class="item"><span class="name">Copper Moth Chili Nachos</span><span class="dots"></span><span class="price">14</span></div>
      <div class="item"><span class="name">Pulled Chicken Nachos</span><span class="dots"></span><span class="price">16</span></div>
      <div class="item"><span class="name">Garlic Roasted Shrimp</span><span class="dots"></span><span class="price">16</span></div>
      <div class="item"><span class="name">Fire Roasted Vegetables Nachos</span><span class="dots"></span><span class="price">14</span></div>
      <h4 class="sec sec--gold sec--small" style="margin-top:8px">FRENCH FRIES</h4>
      <p class="note" style="margin:2px 0">Served with our house made Garlic Aioli and Spicy Ketchup</p>
      <div class="item"><span class="name">Fries Only</span><span class="dots"></span><span class="price price--plain">$7</span></div>
      <div class="item" style="margin-top:2px"><span class="name">Sweet Potato Fries</span><span class="dots"></span><span class="price price--plain">$7</span></div>
      <div class="item" style="margin-top:2px"><span class="name">Cheddar-Jack Cheese Fries</span><span class="dots"></span><span class="price price--plain">$8</span></div>
    </div>
  </div>

  <div class="panel">
    <div class="box" style="height:100%">
      <div class="item" style="margin-top:0"><span class="name">Cheddar-Jack Cheese, Bacon Fries</span><span class="dots"></span><span class="price price--plain">$9</span></div>
      <div class="item" style="margin-top:2px"><span class="name">Chili Cheese Fries</span><span class="dots"></span><span class="price price--plain">$10</span></div>
      <p class="desc">Topped with Copper Moth Chili, cheddar jack cheese and served with chipotle crema on the side.</p>
      <h3 class="sec sec--small" style="margin-top:12px">SOUPS &amp; BOWLS</h3>
      <div class="item"><span class="name">Copper Moth Chili</span><span class="dots"></span><span class="price price--plain">Cup 6 | Bowl 8</span></div>
      <p class="desc">Our signature chili with lean ground beef, black beans, &amp; corn. Topped with cheddar cheese &amp; green onion, served with tri-color tortilla chips.</p>
      <div class="item"><span class="name">Southwestern Sweet Potato Soup</span><span class="dots"></span><span class="price price--plain">Cup 6 | Bowl 8</span></div>
      <p class="desc">A delicious mix of sweet potatoes, corn, bell peppers, and black beans, this vegan soup delivers top flavor and quality with every bowl. Served with tri-color tortilla chips.</p>
      <div class="item"><span class="name">Ancient Grains Bowl</span><span class="dots"></span><span class="price">12</span></div>
      <p class="desc">Quinoa, brown rice, kale and fresh spinach, with fire roasted portobello mushrooms, zucchini and red peppers. Topped with fresh avocado, &amp; feta cheese. Served with Lemon Champagne Vinaigrette</p>
      <div class="item"><span class="name">Grilled Chicken</span><span class="dots"></span><span class="price">5</span></div>
      <div class="item"><span class="name">Garlic Roasted Shrimp</span><span class="dots"></span><span class="price">5</span></div>
      <h3 class="sec sec--small" style="margin-top:10px">SALADS</h3>
      <div class="item"><span class="name">Combo Cat</span><span class="dots"></span><span class="price">11</span></div>
      <p class="desc">Enjoy a side House and a cup of any soup.</p>
      <div class="item"><span class="name">Cat House Salad</span><span class="dots"></span><span class="price">11</span></div>
      <p class="desc">Spring lettuce mix, fresh red peppers, onion, cherry tomatoes, cucumber, and croutons. Served with Red Wine Vinaigrette.</p>
      <div class="item"><span class="name">Grilled Chicken Salad</span><span class="dots"></span><span class="price">15</span></div>
      <p class="desc">Spring lettuce mix, grilled chicken breast, bacon, fresh red peppers, onions, tomatoes, cucumber &amp; feta cheese. Served with Red Wine Vinaigrette.</p>
      <div class="item"><span class="name">Grilled Shrimp Salad*</span><span class="dots"></span><span class="price">16</span></div>
      <p class="desc">Spring lettuce mix, garlic Roasted Shrimp, roasted corn, pico de gallo fresh avocado, Served with Lemon Champagne Vinaigrette</p>
      <div class="item"><span class="name">Goat Cheese Salad</span><span class="dots"></span><span class="price">16</span></div>
      <p class="desc">Spring lettuce mix, fried goat cheese, fresh red peppers, cranberries, white onions, &amp; cherry tomatoes. Served with Red Wine Vinaigrette.</p>
      <div class="item"><span class="name">The Skinny Cat</span><span class="dots"></span><span class="price">14</span></div>
      <div class="item"><span class="name">Combo Cat</span><span class="dots"></span><span class="price">6</span></div>
      <div class="item"><span class="name">Grilled Chicken</span><span class="dots"></span><span class="price">5</span></div>
    </div>
  </div>

  <div class="panel panel--grey">
    <div class="item" style="margin-top:0"><span class="name">Garlic Roasted Shrimp</span><span class="dots"></span><span class="price">5</span></div>
    <div class="item"><span class="name">Fried Goat Cheese</span><span class="dots"></span><span class="price">5</span></div>
    <div class="dress">
      <h3 class="sec sec--gold">DRESSINGS</h3>
      <p class="list" style="text-align:left;font-size:8px">Balsamic Vinaigrette | Caesar Red Wine Vinaigrette | Honey-Mustard | Lemon Champagne Vinaigrette | Ranch | Blue Cheese</p>
    </div>
    <p class="desc" style="margin-top:6px">*The consumption of raw or undercooked eggs, meat, poultry, seafood or shellfish may contribute to food borne illness, especially if you have a medical condition.</p>
    <div class="tags"><span>VEGETARIAN</span><span>SPICY</span></div>
    <h3 class="burgers-head">GOURMET BURGERS &amp;<br>SANDWICHES</h3>
    <p class="desc" style="margin-top:4px">Start with your style and then choose your protein. Our burgers are house made and cooked to your temperature. Our fresh grilled chicken breast is marinated in house with the Quinoa Lentil Burger. All are served on a potato bun with lettuce, tomato, onion, and your choice of hand cut fries or sweet potato fries. <b>Premium sides available for an up charge + $2</b></p>
    <div class="gf"><span>Gluten-Free Bun Available Upon Request | $2</span><span class="gf-icons"><i></i><i></i><i></i></span></div>
    <div class="burger"><span class="name">Calico Cat<p class="desc">Roasted red peppers, red onions, brie cheese, and horseradish aioli.</p></span><span class="p">15.00</span><span class="p">14.00</span><span class="p">13.00</span></div>
    <div class="burger"><span class="name">Tiger Cat<p class="desc">Cheddar, Monterey Jack, and Provolone</p></span><span class="p">15.00</span><span class="p">14.00</span><span class="p">13.00</span></div>
    <div class="burger"><span class="name">Cat Scratch Fever<p class="desc">Guacamole, 3 pepper colby jack, pico de gallo, and chipotle mayo.</p></span><span class="p">15.50</span><span class="p">14.50</span><span class="p">13.50</span></div>
    <div class="burger"><span class="name">The Fat Cat<p class="desc">Fried egg*, bacon, cheddar cheese, and garlic aioli.</p></span><span class="p">16.00</span><span class="p">15.00</span><span class="p">14.00</span></div>
    <div class="burger"><span class="name">Tabby Cat<p class="desc">Melted brie cheese, sliced apple, and citrus aioli.</p></span><span class="p">16.50</span><span class="p">15.50</span><span class="p">14.50</span></div>
    <div class="burger"><span class="name">The Sphynx<p class="desc">Portobello mushrooms, roasted red peppers, smoked gouda cheese, &amp; roasted garlic aioli.</p></span><span class="p">16.50</span><span class="p">15.50</span><span class="p">14.50</span></div>
    <div class="burger"><span class="name">Maine Coon<p class="desc">Grilled shrimp*, roasted corn, swiss cheese, and roasted garlic aioli.</p></span><span class="p">16.50</span><span class="p">15.50</span><span class="p">14.50</span></div>
    <div class="burger"><span class="name">Alley Cat<p class="desc">What's up your alley? Choose a cheese, condiment and one topping.</p></span><span class="p">14.00</span><span class="p">13.00</span><span class="p">12.00</span></div>
    <p class="desc" style="margin-top:4px">Additional Toppings $1 | Bacon, Egg, Shrimp - $2</p>
  </div>
</section>

</body>
</html>
```